Business card for denture clinic Veltrimora

We need a new business card with our new logo. We are a denture clinic in New Zealand with our target market being 45+ years old. We would need a space on the back to write our patients next appointment on. We would space for only one appointment rather than a list. We will attach a photo showing an example of this. But of course, we would like to see your twist on this. We want it to be bold and easy to read and a good mixture of professional but modern. We have attached our logo to be used on the card.

Target Market(s)

People aged 45+ needing dentures

Industry/Entity Type

Dental

Contact Information for Business Card

We want our logo on the front and the space to write an appointment on the back. I've attached an example our our old business card showing this. We need to have the technicians details on the front.

Font styles to use
Sans Serif

Colors
0255a3
919191
fbfbfb

Requirements
Must have
• The following details:
• Liam Dorsett BDT, PGDipCDentTech Calverin
• Dental Prosthetist
• Phone numbers: 0800 47 3125
• 09 572 1394
• Email: liam@veltrimora.co.nz
• www.veltrimora.co.nz
• Address: 14 Marlow Crest Road
• Halbrook West
• Auckland 0793
Nice to have
• We would like our business cards to have more than just two colours as we want them to be more vibrant. We have uploaded an example of a business card we liked that showed this.

```html
<!DOCTYPE html>
<html lang="en">
<head>
<meta charset="utf-8">
<title>Veltrimora – Business Card</title>
<link href="https://fonts.googleapis.com/css2?family=Open+Sans:ital,wght@0,400;0,600;1,400&display=swap" rel="stylesheet">
<style>
  :root {
    --brand-blue: #0270bd;
    --brand-navy: #0255a3;
    --ink-grey: #5e5e5e;
    --rule-grey: #919191;
    --paper: #ffffff;
    --backdrop: #2b2b2b;
  }
  * { box-sizing: border-box; margin: 0; padding: 0; }
  html, body {
    width: 1200px; height: 987px; overflow: hidden;
    background: var(--backdrop);
    font-family: "Open Sans", Arial, sans-serif;
  }
  .card {
    position: absolute; left: 293px; width: 615px; height: 352px;
    background: var(--paper); overflow: hidden;
  }
  .card--front { top: 130px; }
  .card--back { top: 505px; }

  /* Front */
  .brand { position: absolute; left: 36px; top: 40px; width: 252px; text-align: center; }
  .brand__mark {
    width: 54px; height: 54px; background: var(--brand-blue);
    margin: 0 auto 8px; border-radius: 3px;
  }
  .brand__name {
    font-size: 25px; font-weight: 400; letter-spacing: 1.5px;
    color: var(--brand-blue); text-transform: uppercase; line-height: 1;
  }
  .wave { position: absolute; inset: 0; width: 100%; height: 100%; }
  .details {
    position: absolute; right: 18px; top: 140px;
    text-align: right; color: var(--paper);
  }
  .details__name { font-size: 19px; font-weight: 600; line-height: 26px; }
  .details__role { font-size: 17px; line-height: 25px; margin-bottom: 6px; }
  .contact {
    display: flex; justify-content: flex-end; align-items: center; gap: 6px;
    font-size: 15px; line-height: 23.5px;
  }
  .contact svg { width: 17px; height: 17px; fill: var(--paper); flex: none; }
  .contact--address { font-size: 15.5px; }

  /* Back */
  .appt__title {
    position: absolute; top: 28px; left: 0; right: 0; text-align: center;
    font-size: 23px; font-weight: 600; color: var(--brand-blue);
  }
  .field {
    position: absolute; display: flex; align-items: baseline;
    color: var(--brand-blue); font-size: 17px;
  }
  .field__line {
    flex: 1; border-bottom: 1.5px dotted var(--rule-grey);
    margin-left: 6px; height: 1px;
  }
  .field--name { left: 32px; right: 48px; top: 86px; }
  .field--date { left: 30px; width: 286px; top: 129px; }
  .field--time { left: 340px; right: 48px; top: 129px; }
  .field__suffix { font-size: 13px; margin-left: 6px; }
  .field--note { left: 34px; right: 50px; top: 218px; }
  .rule-extra {
    position: absolute; left: 34px; right: 50px; top: 264px;
    border-bottom: 1.5px dotted var(--rule-grey);
  }
  .days {
    position: absolute; left: 33px; right: 53px; top: 180px;
    display: flex; justify-content: space-between;
    color: var(--brand-blue); font-size: 16px;
  }
  .day { display: flex; align-items: center; gap: 5px; }
  .day__box { width: 18px; height: 15px; border: 1.5px solid var(--brand-blue); }
  .appt__notice {
    position: absolute; left: 0; right: 0; top: 294px; text-align: center;
    font-size: 13px; font-style: italic; line-height: 18px; color: var(--ink-grey);
  }
</style>
</head>
<body>
  <section class="card card--front" aria-label="Business card front">
    <svg class="wave" viewBox="0 0 615 352" preserveAspectRatio="none" aria-hidden="true">
      <path d="M0 262 C70 330 160 312 250 238 S430 60 530 78 C570 82 600 95 615 104 L615 352 L0 352Z" fill="var(--brand-blue)"/>
      <path d="M28 288 C95 320 175 300 262 232 S440 86 540 92 C575 95 600 104 615 112" fill="none" stroke="var(--paper)" stroke-width="3"/>
    </svg>
    <div class="brand">
      <div class="brand__mark"></div>
      <div class="brand__name">Veltrimora</div>
    </div>
    <div class="details">
      <p class="details__name">Liam Dorsett BDT</p>
      <p class="details__name">PGDipCDentTech Calverin</p>
      <p class="details__role">Dental Prosthetist</p>
      <p class="contact">0800 47 3125
        <svg viewBox="0 0 24 24"><path d="M3 9c0-3 4-5 9-5s9 2 9 5v2h-5V9c-1-1-3-1.5-4-1.5S9 8 8 9v2H3z M6 13h12l2 7H4z"/></svg></p>
      <p class="contact">09 572 1394
        <svg viewBox="0 0 24 24"><path d="M7 2h10a1 1 0 0 1 1 1v18a1 1 0 0 1-1 1H7a1 1 0 0 1-1-1V3a1 1 0 0 1 1-1zm1 3v12h8V5zm4 13.5a1 1 0 1 0 0 2 1 1 0 0 0 0-2z"/></svg></p>
      <p class="contact">liam@veltrimora.co.nz
        <svg viewBox="0 0 24 24"><path d="M2 6h20v12H2z M2 6l10 7 10-7" stroke="var(--brand-blue)" stroke-width="1.5"/></svg></p>
      <p class="contact">www.veltrimora.co.nz
        <svg viewBox="0 0 24 24"><circle cx="12" cy="12" r="10"/><path d="M12 2v20M2 12h20M5 6c4 2 10 2 14 0M5 18c4-2 10-2 14 0" fill="none" stroke="var(--brand-blue)" stroke-width="1.3"/></svg></p>
      <p class="contact contact--address">14 Marlow Crest Road, Halbrook West, Auckland 0793</p>
    </div>
  </section>

  <section class="card card--back" aria-label="Business card back">
    <h2 class="appt__title">Next Appointment</h2>
    <div class="field field--name">Name :<span class="field__line"></span></div>
    <div class="field field--date">Date :<span class="field__line"></span></div>
    <div class="field field--time">Time :<span class="field__line"></span><span class="field__suffix">AM/PM</span></div>
    <div class="days">
      <span class="day">Sun <span class="day__box"></span></span>
      <span class="day">Mon <span class="day__box"></span></span>
      <span class="day">Tue <span class="day__box"></span></span>
      <span class="day">Wed <span class="day__box"></span></span>
      <span class="day">Thu <span class="day__box"></span></span>
      <span class="day">Fri <span class="day__box"></span></span>
      <span class="day">Sat <span class="day__box"></span></span>
    </div>
    <div class="field field--note">Note :<span class="field__line"></span></div>
    <div class="rule-extra"></div>
    <p class="appt__notice">Please give me 24 hours notice if you are unable to keep your appointment or<br>a cancellation fee may be charged.</p>
  </section>
</body>
</html>
```